Business Card for a mobile physiotherapy company

I need a layout for a business card for a mobile physiotherapy company.
Slogan is "Mobile Physiotherapy - Your Road To Recovery"
Phone number is 867-555-0142
Email VardenTherapy@postnest.ca (subject to change with website)
Website www.VardenTherapy.ca
My name and credentials: Luke Varden Luke Varden, BSc(kin), MPT, CAFCI, IMS
Information maybe included: Direct Billing, Services including Physiotherapy, IMS, acupuncture
Maybe include facebook and instagram logos
One side with the logo clean and sharp
Other side with details, try not to look too busy, keep everything concise

```html
<!DOCTYPE html>
<html lang="en">
<head>
<meta charset="utf-8">
<title>Varden Therapy — Business Card</title>
<link rel="stylesheet" href="https://fonts.googleapis.com/css2?family=Lato:wght@400;700&family=Roboto:wght@400&display=swap">
<style>
  :root {
    --backdrop: #121212;
    --card: #1d1d1d;
    --card-edge: #262626;
    --ink-light: #d9d9d9;
    --ink-mid: #bdbdbd;
    --ink-emboss: #2e2e2e;
    --divider: #4a4a4a;
  }
  * { margin: 0; padding: 0; box-sizing: border-box; }
  html, body {
    width: 1200px;
    height: 900px;
    overflow: hidden;
    background: var(--backdrop);
  }
  .stage {
    width: 1200px;
    height: 900px;
    display: flex;
    flex-direction: column;
    align-items: center;
    justify-content: center;
    gap: 44px;
  }
  .card {
    width: 672px;
    height: 384px;
    background: var(--card);
    border: 1px solid var(--card-edge);
    position: relative;
  }

  /* Front side */
  .card--front {
    display: flex;
    align-items: center;
    justify-content: center;
  }
  .brand {
    display: flex;
    align-items: center;
    gap: 16px;
    font-family: "Lato", sans-serif;
    font-weight: 700;
    letter-spacing: 0.14em;
    text-transform: uppercase;
  }
  .brand__square {
    width: 18px;
    height: 18px;
  }
  .card--front .brand { color: var(--ink-light); font-size: 40px; }
  .card--front .brand__square { background: var(--ink-light); }

  /* Back side */
  .card--back {
    display: flex;
    align-items: center;
    padding: 0 40px 0 44px;
  }
  .card--back .brand {
    color: var(--ink-emboss);
    font-size: 26px;
    width: 250px;
    gap: 12px;
  }
  .card--back .brand__square { background: var(--ink-emboss); width: 14px; height: 14px; }
  .divider {
    width: 1px;
    height: 250px;
    background: var(--divider);
    margin: 0 34px 0 20px;
  }
  .details { color: var(--ink-light); }
  .details__name {
    font-family: "Roboto", sans-serif;
    font-size: 25px;
    line-height: 1.22;
    margin-bottom: 8px;
  }
  .details__services {
    font-family: "Lato", sans-serif;
    font-size: 15px;
    line-height: 1.45;
    color: var(--ink-mid);
    margin-bottom: 14px;
  }
  .contact { list-style: none; font-family: "Lato", sans-serif; font-size: 17px; }
  .contact__item {
    display: flex;
    align-items: center;
    gap: 12px;
    margin-bottom: 9px;
  }
  .contact__icon { width: 12px; height: 12px; flex: none; }
</style>
</head>
<body>
  <main class="stage">
    <section class="card card--front" aria-label="Card front">
      <div class="brand"><span class="brand__square"></span>Varden Therapy</div>
    </section>

    <section class="card card--back" aria-label="Card back">
      <div class="brand"><span class="brand__square"></span>Varden Therapy</div>
      <div class="divider"></div>
      <div class="details">
        <p class="details__name">Luke Varden, BSc(kin),<br>MPT, CAFCI, IMS</p>
        <p class="details__services">Direct Billing, Services including<br>Physiotherapy, IMS, acupuncture</p>
        <ul class="contact">
          <li class="contact__item">
            <svg class="contact__icon" viewBox="0 0 12 12" aria-hidden="true"><path d="M2.5 1 L4.5 1 L5.2 3.6 L4 4.6 C4.6 6 6 7.4 7.4 8 L8.4 6.8 L11 7.5 L11 9.5 C11 10.4 10.3 11 9.5 11 C5 10.6 1.4 7 1 2.5 C1 1.7 1.6 1 2.5 1 Z" fill="none" stroke="#bdbdbd" stroke-width="1"/></svg>
            867-555-0142
          </li>
          <li class="contact__item">
            <svg class="contact__icon" viewBox="0 0 12 12" aria-hidden="true"><rect x="1" y="2.5" width="10" height="7" fill="none" stroke="#bdbdbd" stroke-width="1"/><path d="M1 2.5 L6 6.5 L11 2.5" fill="none" stroke="#bdbdbd" stroke-width="1"/></svg>
            VardenTherapy@postnest.ca
          </li>
          <li class="contact__item">
            <svg class="contact__icon" viewBox="0 0 12 12" aria-hidden="true"><circle cx="6" cy="6" r="5" fill="none" stroke="#bdbdbd" stroke-width="1"/><ellipse cx="6" cy="6" rx="2.2" ry="5" fill="none" stroke="#bdbdbd" stroke-width="1"/><path d="M1 6 H11" stroke="#bdbdbd" stroke-width="1"/></svg>
            www.VardenTherapy.ca
          </li>
        </ul>
      </div>
    </section>
  </main>
</body>
</html>
```